Brief 1.
An Overview / Background of the Business & Services-
It is a new business being set up. Our business is to design a solution to enable Alumni of higher institutions in Nigeria apply for their academic transcript through our system. the name of our product will be Record Relay Nigeria. We need logo, site banner, advert banner and several academic images. See www.rrly-ng.example for more insight.
The Target Market / Audience you are trying to reach-
Alumni of Nigeria Universities, usually between the ages of 20-40.
Design Specifics; any preferences or ideas for Style, Colour, Imagery, etc-
Color scheme will be several shades of light blue and white. Please check www.rrly-ng.example for more insight.

Brief 2

Pantrybasket.com is an online food and grocery shop, we supply fresh food stuff and other daily essential needs on request to customers. The site is already up (www.pantrybasket.example). We need logo, site rolling banner, advert banner and several offer graphics as shown in the placeholder images in the site now.
Working women in Nigeria.
Color scheme will be several shades of light Green and White. Please check the site.

```html
<!DOCTYPE html>
<html lang="en">
<head>
<meta charset="utf-8">
<title>Pantry Basket – Online Food &amp; Grocery Shop</title>
<link href="https://fonts.googleapis.com/css2?family=Open+Sans:wght@400;600;700;800&display=swap" rel="stylesheet">
<style>
:root{
  --green:#7dbb34;
  --green-dark:#5e9a1f;
  --teal:#33b29d;
  --teal-dark:#23917f;
  --ink:#333;
  --muted:#888;
  --line:#e3e3e3;
  --dark:#2f2f2f;
  --darker:#1f1f1f;
  --blue:#3aa6c9;
  --white:#fff;
}
*{box-sizing:border-box;margin:0;padding:0}
html,body{width:1200px;height:2244px;overflow:hidden;background:var(--white)}
body{font-family:"Open Sans",Arial,sans-serif;color:var(--ink);position:relative}
a{color:inherit;text-decoration:none}
.abs{position:absolute}

/* header */
.top-links{right:100px;top:22px;font-size:13px;color:#666;letter-spacing:.5px}
.top-links span{margin-left:22px}
.brand{left:100px;top:38px;display:flex;align-items:center;gap:16px}
.brand-dot{width:74px;height:74px;border-radius:50%;background:var(--green)}
.brand-name{font-size:40px;font-weight:700;color:var(--green);line-height:1}
.brand-tag{font-size:14px;color:var(--muted);margin-top:6px}
.cart-mini{left:760px;top:70px;font-size:12px;color:#666;display:flex;gap:8px;align-items:center}
.search{left:890px;top:66px;width:210px;height:34px;border:1px solid var(--line);display:flex}
.search input{flex:1;border:0;padding:0 10px;font:13px "Open Sans",sans-serif;color:#aaa}
.search button{width:34px;border:0;background:var(--green)}

/* nav */
.nav{left:0;top:160px;width:1200px;height:38px;background:var(--teal)}
.nav ul{list-style:none;display:flex;margin-left:100px;height:38px}
.nav li{color:#fff;font-size:14px;font-weight:600;padding:0 20px;line-height:38px}
.nav li.active{background:var(--teal-dark)}

/* hero */
.hero{left:40px;top:212px;width:724px;height:420px;background:linear-gradient(135deg,#c9c2b3,#8b6a4c 55%,#4b3a2c)}
.hero-caption{left:64px;top:532px;}
.hero-caption .t{background:rgba(125,187,52,.92);color:#fff;font-size:28px;font-weight:600;padding:6px 14px;display:inline-block}
.hero-caption .s{background:var(--green-dark);color:#fff;font-size:13px;padding:5px 14px;display:inline-block;margin-top:4px}
.promo{left:780px;width:380px;padding:22px 24px;color:#fff}
.promo h3{font-size:30px;font-weight:800;line-height:1.15}
.promo p{font-size:14px;margin-top:8px}
.promo .btn{display:inline-block;margin-top:14px;background:var(--darker);font-size:11px;padding:5px 12px;color:#fff}
.promo-1{top:212px;height:196px;background:var(--darker)}
.promo-1 h3 span{color:var(--green)}
.promo-1 .btn{background:var(--green)}
.promo-2{top:416px;height:216px;background:var(--green)}
.arrow{top:395px;width:40px;height:56px;background:rgba(150,150,150,.7)}

/* sidebar */
.side{left:100px;width:240px}
.side h2{font-size:24px;font-weight:600;color:var(--teal);border-bottom:2px solid var(--teal);padding-bottom:6px}
.cats{list-style:none}
.cats li{font-size:14px;color:#555;padding:8px 6px;border-bottom:1px solid var(--line)}
.side-btn{display:block;background:var(--green);color:#fff;font-size:16px;padding:10px 14px;margin-bottom:12px}
.hurry{height:270px;background:linear-gradient(160deg,#f5f1ea,#d9cbb3 60%,#a89376);position:relative}
.hurry .pct{position:absolute;left:12px;top:10px;background:var(--green);color:#fff;font-weight:800;font-size:20px;padding:4px 8px}
.hurry .msg{position:absolute;left:14px;bottom:24px;font-size:30px;color:#fff;line-height:1.1}
.mini{display:flex;gap:14px;padding:14px 0;border-bottom:1px solid var(--line)}
.mini .pic{width:80px;height:56px;background:linear-gradient(135deg,#f1d2cb,#c84a40)}
.mini .n{font-size:13px}
.mini .p{font-size:13px;color:var(--green-dark);margin-top:4px}

/* main */
.main{left:360px;width:740px}
.head{font-size:24px;font-weight:600;color:#333;border-bottom:1px solid var(--line);padding-bottom:6px;position:relative}
.head::after{content:"";position:absolute;right:0;top:6px;width:20px;height:20px;background:#bbb}
.grid{display:grid;grid-template-columns:repeat(4,176px);gap:12px}
.prod .pic{height:126px}
.prod .n{font-size:13px;text-align:center;margin-top:8px}
.prod .p{font-size:13px;text-align:center;color:var(--green-dark);margin-top:2px}
.g1{background:linear-gradient(135deg,#5b3d5e,#2b2333)}
.g2{background:linear-gradient(135deg,#7aa84b,#c0392b)}
.g3{background:linear-gradient(135deg,#e8e4e1,#9aa6b0)}
.g4{background:linear-gradient(135deg,#c9c3b8,#6a7a8a)}
.g5{background:linear-gradient(135deg,#d9462f,#7c1d14)}
.g6{background:linear-gradient(135deg,#f1c9a2,#c96f3e)}
.g7{background:linear-gradient(135deg,#4d8a2b,#e4b43a)}
.g8{background:linear-gradient(135deg,#ece7df,#b9a48a)}
.g9{background:linear-gradient(135deg,#8b5a3c,#3d2a1f)}
.g10{background:linear-gradient(135deg,#cf3a2b,#f2b24b)}
.g11{background:linear-gradient(135deg,#d9d3cf,#8a8a92)}
.g12{background:linear-gradient(135deg,#f08a5d,#b8452a)}
.strip{display:flex;gap:12px}
.ship{width:364px;height:100px;background:var(--blue);color:#fff;padding:14px 18px}
.ship b{font-size:26px;display:block;line-height:1}
.ship span{font-size:13px}
.call{width:364px;height:100px;background:var(--green);color:#fff;padding:14px 18px;display:flex;justify-content:space-between}
.call b{font-size:30px;display:block;line-height:1}
.call span{font-size:14px}
.call .pic{width:120px;background:linear-gradient(135deg,#f7e1c7,#d4a173)}
.adbar{left:364px;top:1808px;width:736px;height:86px;background:linear-gradient(90deg,#c98a4d,#9d5e2c 30%,#2d2d2d 40%,#1f1f1f);display:flex;align-items:center;justify-content:flex-end;padding-right:30px;gap:20px;color:#fff;font-size:22px}
.adbar .hl{color:var(--green);font-weight:700}
.adbar .btn{background:var(--green);font-size:12px;padding:6px 14px}

/* footer */
.footer{left:0;top:1930px;width:1200px;height:262px;background:var(--dark);color:#bbb;padding:34px 100px}
.fcols{display:flex}
.fcol{width:250px}
.fcol h4{color:#fff;font-size:14px;font-weight:600;margin-bottom:12px}
.fcol li{list-style:none;font-size:12px;line-height:20px}
.two{display:flex;gap:30px}
.social{display:flex;gap:6px;margin-top:16px}
.social i{width:24px;height:24px;background:#555;display:block}
.pay{display:flex;gap:6px;margin-top:16px}
.pay i{width:40px;height:24px;background:#e9e9e9;display:block}
.copy{left:0;top:2192px;width:1200px;height:52px;background:var(--darker);color:#999;font-size:12px;text-align:center;line-height:52px}
</style>
</head>
<body>

<div class="abs top-links"><span>MY ACCOUNT</span><span>MY WISHLIST</span><span>MY CART</span><span>CHECKOUT</span><span>LOG IN</span></div>
<div class="abs brand">
  <div class="brand-dot"></div>
  <div><div class="brand-name">Pantry Basket</div><div class="brand-tag">Fresh food every day</div></div>
</div>
<div class="abs cart-mini">
  <svg width="22" height="20" viewBox="0 0 22 20"><path d="M1 2h4l3 11h11l2-8H7" fill="none" stroke="#7dbb34" stroke-width="2"/><circle cx="9" cy="17" r="2" fill="#7dbb34"/><circle cx="18" cy="17" r="2" fill="#7dbb34"/></svg>
  <span>0 items<br>$0.00</span>
</div>
<div class="abs search"><input value="Search"><button aria-label="Search"><svg width="16" height="16" viewBox="0 0 16 16"><circle cx="7" cy="7" r="5" fill="none" stroke="#fff" stroke-width="2"/><path d="M11 11l4 4" stroke="#fff" stroke-width="2"/></svg></button></div>

<nav class="abs nav"><ul><li class="active">HOME</li><li>HEALTH &amp; WELLNESS</li><li>FRUITS &amp; VEG</li><li>POULTRY, MEAT &amp; FISH</li><li>FOOD STUFFS</li><li>RECIPES</li><li>OTHERS</li></ul></nav>

<div class="abs hero" role="img" aria-label="Plated fresh seafood dish"></div>
<div class="abs hero-caption"><div class="t">Fresh Natural Sea Food</div><br><div class="s">Ready food from the sea</div></div>
<div class="abs arrow" style="left:0"><svg width="40" height="56"><path d="M24 18l-10 10 10 10" stroke="#fff" stroke-width="3" fill="none"/></svg></div>
<div class="abs arrow" style="left:1160px"><svg width="40" height="56"><path d="M16 18l10 10-10 10" stroke="#fff" stroke-width="3" fill="none"/></svg></div>
<div class="abs promo promo-1"><h3><span>FREE DELIVERY &amp;</span><br>GET 10% DISCOUNT</h3><p>Every Registered Users</p><span class="btn">Read More</span></div>
<div class="abs promo promo-2"><h3>HERBAL &amp;<br>AYURVEDIC &amp; SPA<br>PRODUCTS</h3><p>Aliquam erat volutpat</p><span class="btn">Read More</span></div>

<aside class="abs side" style="top:690px">
  <h2>Categories</h2>
  <ul class="cats"><li>All</li><li>Health &amp; Wellness</li><li>Fruits &amp; Veg</li><li>Poultry, Meat &amp; Fish</li><li>Food Stuffs</li><li>Recipes</li><li>Others</li></ul>
  <div style="height:28px"></div>
  <a class="side-btn">My Cart - 0 items</a>
  <a class="side-btn">Compare Products</a>
  <div class="hurry" role="img" aria-label="Shopper with grocery bags"><span class="pct">50%</span><span class="msg">Hurry offer<br>ends soon</span></div>
  <h2 style="margin-top:22px">Latest Products</h2>
  <div class="mini"><div class="pic" role="img" aria-label="Red snapper fish"></div><div><div class="n">Red Snapper (1kg)</div><div class="p">$1,000.00</div></div></div>
  <div class="mini"><div class="pic" role="img" aria-label="Red snapper fish"></div><div><div class="n">Red Snapper (1kg)</div><div class="p">$1,000.00</div></div></div>
  <div class="mini"><div class="pic" role="img" aria-label="Red snapper fish"></div><div><div class="n">Red Snapper (1kg)</div><div class="p">$1,000.00</div></div></div>
</aside>

<main class="abs main" style="top:690px">
  <h2 class="head">Latest Products</h2>
  <div class="grid" style="margin-top:14px">
    <div class="prod"><div class="pic g1" role="img" aria-label="Fresh berries"></div><div class="n">Cras accumsan felis</div><div class="p">$1,000.00</div></div>
    <div class="prod"><div class="pic g2" role="img" aria-label="Assorted vegetables"></div><div class="n">Cras accumsan felis</div><div class="p">$1,000.00</div></div>
    <div class="prod"><div class="pic g3" role="img" aria-label="Fresh fish"></div><div class="n">Cras accumsan felis</div><div class="p">$1,000.00</div></div>
    <div class="prod"><div class="pic g4" role="img" aria-label="Whole fish on ice"></div><div class="n">Cras accumsan felis</div><div class="p">$1,000.00</div></div>
  </div>
  <div class="strip" style="margin-top:20px">
    <div class="ship"><b>Free Shipping</b><span>on orders over $50 nationwide</span></div>
    <div class="call"><div><b>Give us call</b><span>1-800-555-0142</span></div><div class="pic" role="img" aria-label="Customer support agent"></div></div>
  </div>
  <h2 class="head" style="margin-top:30px">Featured Products</h2>
  <div class="grid" style="margin-top:14px;row-gap:22px">
    <div class="prod"><div class="pic g5" role="img" aria-label="Raw meat cuts"></div><div class="n">Cras accumsan felis</div><div class="p">$1,000.00</div></div>
    <div class="prod"><div class="pic g6" role="img" aria-label="Fresh chicken"></div><div class="n">Cras accumsan felis</div><div class="p">$1,000.00</div></div>
    <div class="prod"><div class="pic g7" role="img" aria-label="Fruit basket"></div><div class="n">Cras accumsan felis</div><div class="p">$1,000.00</div></div>
    <div class="prod"><div class="pic g8" role="img" aria-label="Grains and beans"></div><div class="n">Cras accumsan felis</div><div class="p">$1,000.00</div></div>
    <div class="prod"><div class="pic g9" role="img" aria-label="Spices in bowls"></div><div class="n">Cras accumsan felis</div><div class="p">$1,000.00</div></div>
    <div class="prod"><div class="pic g10" role="img" aria-label="Tomatoes and peppers"></div><div class="n">Cras accumsan felis</div><div class="p">$1,000.00</div></div>
    <div class="prod"><div class="pic g11" role="img" aria-label="Fresh fish fillets"></div><div class="n">Cras accumsan felis</div><div class="p">$1,000.00</div></div>
    <div class="prod"><div class="pic g12" role="img" aria-label="Salmon steaks"></div><div class="n">Cras accumsan felis</div><div class="p">$1,000.00</div></div>
    <div class="prod"><div class="pic g3" role="img" aria-label="Seafood platter"></div><div class="n">Cras accumsan felis</div><div class="p">$1,000.00</div></div>
    <div class="prod"><div class="pic g10" role="img" aria-label="Fresh produce"></div><div class="n">Cras accumsan felis</div><div class="p">$1,000.00</div></div>
    <div class="prod"><div class="pic g12" role="img" aria-label="Grilled salmon"></div><div class="n">Cras accumsan felis</div><div class="p">$1,000.00</div></div>
    <div class="prod"><div class="pic g8" role="img" aria-label="Bread and pastries"></div><div class="n">Cras accumsan felis</div><div class="p">$1,000.00</div></div>
  </div>
</main>

<div class="abs adbar" role="img" aria-label="Advert banner with fresh produce"><span>Phasellus et <span class="hl">pulvinar</span> tellus accumsan.</span><span class="btn">Learn More</span></div>

<footer class="abs footer">
  <div class="fcols">
    <div class="fcol" style="width:300px">
      <h4>Navigation Menu</h4>
      <div class="two">
        <ul><li>All</li><li>Health &amp; Wellness</li><li>Fruits &amp; Veg</li><li>Poultry, Meat &amp; Fish</li></ul>
        <ul><li>Food Stuffs</li><li>Recipes</li><li>Others</li></ul>
      </div>
      <div class="social"><i></i><i></i><i></i><i></i><i></i></div>
    </div>
    <div class="fcol">
      <h4>Customer Service</h4>
      <ul><li>About Us</li><li>Delivery Information</li><li>Privacy Policy</li><li>Term &amp; Condition</li></ul>
      <div class="pay"><i></i><i></i><i></i><i></i></div>
    </div>
    <div class="fcol">
      <h4>My Account</h4>
      <ul><li>My Product</li><li>My Orders</li><li>My Address</li><li>My Personal Info</li></ul>
    </div>
    <div class="fcol">
      <h4>Other Links</h4>
      <ul><li>Site Map</li><li>Search Terms</li><li>Advanced Search</li><li>Orders and Returns</li><li>Contact Us</li></ul>
    </div>
  </div>
</footer>
<div class="abs copy">Copyright © 2014. Pantrybasket.com - All rights reserved</div>

</body>
</html>
```